Velmora Battery Saver App UI design.

We need a mockup layout design of an Velmora app uncoded. This simple battery saver app is composed primarily by three screens described in the attached specification. After the mockup approved we need the UI elements sliced, the app icon and a banner for the nook mart.

```html
<!DOCTYPE html>
<html lang="en">
<head>
<meta charset="utf-8">
<title>Velmora Battery Saver – History</title>
<link rel="stylesheet" href="https://fonts.googleapis.com/css2?family=Raleway:wght@400;500;600&family=Roboto:wght@400;500;700&display=swap">
<style>
  :root {
    --bg-top: #4a5f78;
    --bg-bottom: #1f2733;
    --green: #3fcf7c;
    --green-dark: #33b86a;
    --green-text: #3ccf74;
    --blue: #27a3c7;
    --tab-bg: #f4f7f5;
    --row-bg: #1c1c1c;
    --row-bg-alt: #222222;
    --row-line: #2e2e2e;
    --text-light: #f2f2f2;
    --text-muted: #bdbdbd;
    --nav-bg: #111111;
  }
  * { box-sizing: border-box; margin: 0; padding: 0; }
  html, body {
    width: 1200px; height: 962px; overflow: hidden;
    background: linear-gradient(160deg, var(--bg-top), var(--bg-bottom));
    font-family: "Roboto", sans-serif;
  }
  .screen {
    position: absolute; left: 384px; top: 97px;
    width: 432px; height: 768px;
    background: var(--row-bg);
    overflow: hidden;
    box-shadow: 0 20px 60px rgba(0,0,0,.45);
    display: flex; flex-direction: column;
  }
  .status-bar {
    height: 26px; background: var(--green-dark);
    display: flex; justify-content: flex-end; align-items: center; gap: 6px;
    padding: 0 10px; color: #fff; font-size: 14px;
  }
  .status-bar svg { display: block; }
  .app-bar {
    height: 58px; background: var(--green);
    display: flex; align-items: center; gap: 14px; padding: 0 16px;
    color: #fff; font-family: "Raleway", sans-serif; font-size: 20px; font-weight: 500;
  }
  .app-mark { width: 26px; height: 26px; background: #fff; border-radius: 4px; }
  .tabs {
    height: 44px; background: var(--tab-bg);
    display: flex; font-family: "Raleway", sans-serif; font-size: 14px; font-weight: 500;
    letter-spacing: .5px;
  }
  .tab { flex: 1; display: flex; align-items: center; justify-content: center; position: relative; }
  .tab--active { color: var(--green-text); }
  .tab--active::after {
    content: ""; position: absolute; left: 20%; right: 20%; bottom: 0; height: 3px; background: var(--green);
  }
  .tab--current { color: var(--blue); }
  .log-count {
    height: 38px; background: var(--green);
    display: flex; align-items: center; justify-content: center;
    color: #fff; font-family: "Raleway", sans-serif; font-size: 14px; letter-spacing: .5px;
  }
  .log-list { flex: 1; display: flex; flex-direction: column; }
  .log-item {
    height: 106px; display: flex; border-bottom: 1px solid var(--row-line);
    background: var(--row-bg-alt);
  }
  .log-item:nth-child(even) { background: var(--row-bg); }
  .log-item__stripe { width: 8px; }
  .log-item--unplugged .log-item__stripe { background: var(--blue); }
  .log-item--charging .log-item__stripe { background: var(--green); }
  .log-item__main { flex: 1.15; padding: 18px 14px; display: flex; flex-direction: column; gap: 3px; }
  .log-item__state { font-family: "Raleway", sans-serif; font-size: 19px; letter-spacing: .3px; }
  .log-item--unplugged .log-item__state { color: var(--blue); }
  .log-item--charging .log-item__state { color: var(--green-text); }
  .log-item__note { font-size: 12px; color: var(--text-muted); }
  .log-item__stamp { display: flex; gap: 28px; font-size: 14px; font-weight: 500; color: var(--text-light); margin-top: 6px; }
  .log-item__side {
    flex: 1; border-left: 1px solid var(--row-line);
    display: flex; flex-direction: column; align-items: flex-end; justify-content: center; gap: 10px;
    padding-right: 20px;
  }
  .log-item__level { font-size: 16px; font-weight: 700; }
  .log-item--unplugged .log-item__level { color: var(--blue); }
  .log-item--charging .log-item__level { color: var(--green-text); }
  .log-item__reading { font-size: 14px; font-weight: 500; color: var(--text-light); }
  .log-item--fade { opacity: .35; }
  .nav-bar {
    height: 56px; background: var(--nav-bg);
    display: flex; align-items: center; justify-content: space-around;
  }
</style>
</head>
<body>
  <main class="screen">
    <div class="status-bar">
      <svg width="16" height="14" viewBox="0 0 16 14"><path d="M8 13 L0 4 A11 11 0 0 1 16 4 Z" fill="#fff"/></svg>
      <svg width="14" height="14" viewBox="0 0 14 14"><path d="M14 0 V14 H0 Z" fill="#fff"/></svg>
      <svg width="9" height="15" viewBox="0 0 9 15"><rect x="0" y="2" width="9" height="13" rx="1" fill="#fff"/><rect x="3" y="0" width="3" height="2" fill="#fff"/></svg>
      <span class="status-bar__time">12:06</span>
    </div>
    <header class="app-bar">
      <span class="app-mark"></span>
      <span class="app-bar__title">Velmora Charge Keeper</span>
    </header>
    <nav class="tabs">
      <div class="tab tab--active">HISTORY</div>
      <div class="tab tab--current">CURRENT</div>
    </nav>
    <div class="log-count">336 LOG ITEMS</div>

    <section class="log-list">
      <article class="log-item log-item--unplugged">
        <span class="log-item__stripe"></span>
        <div class="log-item__main">
          <span class="log-item__state">UNPLUGGED</span>
          <span class="log-item__note">After 0.8 hours plugged in</span>
          <span class="log-item__stamp"><span>24/09/2014</span><span>23:04</span></span>
        </div>
        <div class="log-item__side">
          <span class="log-item__level">100%</span>
          <span class="log-item__reading">39.5°C / 4.167V</span>
        </div>
      </article>
      <article class="log-item log-item--charging">
        <span class="log-item__stripe"></span>
        <div class="log-item__main">
          <span class="log-item__state">CHARGING (USB)</span>
          <span class="log-item__stamp"><span>24/09/2014</span><span>23:04</span></span>
        </div>
        <div class="log-item__side">
          <span class="log-item__level">100%</span>
          <span class="log-item__reading">34.9°C / 4.329V</span>
        </div>
      </article>
      <article class="log-item log-item--unplugged">
        <span class="log-item__stripe"></span>
        <div class="log-item__main">
          <span class="log-item__state">UNPLUGGED</span>
          <span class="log-item__note">After 2.0 hours plugged in</span>
          <span class="log-item__stamp"><span>24/09/2014</span><span>22:11</span></span>
        </div>
        <div class="log-item__side">
          <span class="log-item__level">100%</span>
          <span class="log-item__reading">37.5°C / 4.21V</span>
        </div>
      </article>
      <article class="log-item log-item--charging">
        <span class="log-item__stripe"></span>
        <div class="log-item__main">
          <span class="log-item__state">CHARGING (USB)</span>
          <span class="log-item__stamp"><span>24/09/2014</span><span>20:58</span></span>
        </div>
        <div class="log-item__side">
          <span class="log-item__level">100%</span>
          <span class="log-item__reading">30.2°C / 4.33V</span>
        </div>
      </article>
      <article class="log-item log-item--charging log-item--fade">
        <span class="log-item__stripe"></span>
        <div class="log-item__main">
          <span class="log-item__state">CHARGING (USB)</span>
          <span class="log-item__stamp"><span>24/09/2014</span><span>20:58</span></span>
        </div>
        <div class="log-item__side">
          <span class="log-item__level">100%</span>
          <span class="log-item__reading">30.0°C / 4.32V</span>
        </div>
      </article>
    </section>

    <nav class="nav-bar">
      <svg width="30" height="22" viewBox="0 0 30 22" aria-label="Back"><path d="M8 4 H20 A7 7 0 0 1 20 18 H6 M8 4 L4 8 M8 4 L4 0" fill="none" stroke="#eee" stroke-width="2" transform="translate(2 2)"/></svg>
      <svg width="34" height="22" viewBox="0 0 34 22" aria-label="Home"><path d="M2 20 L9 3 H25 L32 20 Z" fill="none" stroke="#eee" stroke-width="2"/></svg>
      <svg width="28" height="24" viewBox="0 0 28 24" aria-label="Recent apps"><rect x="2" y="8" width="22" height="14" fill="none" stroke="#eee" stroke-width="2"/><path d="M6 4 H27 V18" fill="none" stroke="#eee" stroke-width="2"/></svg>
    </nav>
  </main>
</body>
</html>
```